Export company based in South America (Ecuador) we export flowers, chocolate, and bananas

We need a website that gives our potential clients and introduction into our company and the different types of commodities we export around the world. We are based in Quito, Ecuador so the website should portray the feel of Ecuadorian landscapes within a modern looking website.
At the moment we are exporting roses, chocolate, and bananas so the website should have an intro to our company and then three different areas that describe our three main commodity. The three different sections should explain why each of the products from Ecuador are some of the best in the world in their categories and the benefits of importing the commodity through our company.
Industry/Entity Type
Commodity
Number of Pages Required
4 page

```html
<!DOCTYPE html>
<html lang="en">
<head>
<meta charset="utf-8">
<title>Alturo Export</title>
<link href="https://fonts.googleapis.com/css2?family=Titillium+Web:wght@400;600;700&family=Lato:wght@400;700&display=swap" rel="stylesheet">
<style>
:root{
  --navy:#1c3d7a;
  --navy-deep:#0f2a5c;
  --blue:#1f4f9a;
  --orange:#ef4a25;
  --ink:#222;
  --text:#555;
  --line:#dcdcdc;
  --light:#f4f4f4;
  --footer:#232323;
}
*{margin:0;padding:0;box-sizing:border-box}
html,body{width:1200px;height:5226px;overflow:hidden}
body{font-family:"Lato",sans-serif;color:var(--text);background:#fff;position:relative}
.abs{position:absolute}
h1,h2,h3,h4{font-family:"Titillium Web",sans-serif;color:var(--ink)}
.section-title{position:absolute;left:0;width:1200px;text-align:center;font-size:36px;font-weight:700;text-transform:uppercase;letter-spacing:.5px}
.underline{position:absolute;left:570px;width:60px;height:4px;background:var(--navy)}
.btn{display:inline-block;font-family:"Titillium Web",sans-serif;font-weight:700;color:#fff;text-transform:uppercase;border-radius:3px;text-align:center}

/* header */
.header{position:absolute;left:0;top:0;width:1200px;height:142px;background:#fff}
.brand{position:absolute;left:140px;top:30px;display:flex;align-items:center;gap:10px}
.brand .dot{width:56px;height:56px;border-radius:50%;background:var(--navy)}
.brand span{font-family:"Titillium Web",sans-serif;font-weight:700;font-size:30px;color:var(--ink);letter-spacing:1px}
.tollfree{position:absolute;left:572px;top:26px;display:flex;align-items:center;gap:10px}
.tollfree .ico{width:36px;height:36px;border-radius:50%;background:var(--orange);display:flex;align-items:center;justify-content:center}
.tollfree small{display:block;font-size:12px;color:#555}
.tollfree b{display:block;font-family:"Titillium Web",sans-serif;font-size:22px;color:var(--ink);line-height:1}
.search{position:absolute;left:820px;top:32px;width:235px;height:32px;border:1px solid #bbb;border-radius:16px;font-size:11px;color:#999;padding:8px 16px}
.search svg{position:absolute;right:10px;top:8px}
.navbar{position:absolute;left:290px;top:93px;width:910px;height:49px;background:var(--navy-deep);clip-path:polygon(28px 0,100% 0,100% 100%,0 100%)}
.navbar ul{list-style:none;display:flex;gap:0;position:absolute;left:40px;top:0;height:49px;align-items:center}
.navbar li{font-family:"Titillium Web",sans-serif;font-weight:700;font-size:14px;color:#fff;padding:0 18px;text-transform:uppercase}
.navbar li.active{text-decoration:underline;text-underline-offset:6px}

/* hero */
.hero{position:absolute;left:0;top:142px;width:1200px;height:673px;background:linear-gradient(180deg,#6b6a66 0%,#8a7450 25%,#3c3a3a 55%,#2a2a30 100%);clip-path:polygon(0 0,100% 0,100% 610px,0 100%)}
.hero-text{position:absolute;left:0;top:222px;width:1200px;text-align:center;color:#fff}
.hero-text h1{color:#fff;font-size:80px;font-weight:700;line-height:1}
.hero-text p{font-size:19px;line-height:26px;margin-top:18px}
.hero-text .btn{background:var(--orange);font-size:14px;padding:10px 28px;margin-top:22px}
.dots{position:absolute;top:706px;left:565px;display:flex;gap:8px}
.dots i{width:18px;height:18px;border-radius:50%;border:2px solid #fff;display:block}
.dots i.on{background:#fff}

/* products */
.card{position:absolute;top:983px;width:281px;height:487px;border:1px solid var(--line);background:#fff;text-align:center}
.card .photo{height:189px}
.card .badge{position:absolute;left:98px;top:148px;width:84px;height:84px;border-radius:50%;background:var(--orange);border:4px solid #fff;display:flex;align-items:center;justify-content:center}
.card h3{font-size:18px;font-weight:600;margin-top:70px;text-transform:uppercase}
.card p{font-size:13px;line-height:22px;padding:0 26px;margin-top:8px}
.card .btn{background:var(--navy-deep);font-size:12px;padding:6px 18px;margin-top:18px}

/* welcome */
.welcome{position:absolute;left:0;top:1578px;width:1200px;height:497px;background:var(--blue)}
.welcome .photo{position:absolute;left:0;top:0;width:600px;height:497px;background:linear-gradient(135deg,#8da3b8 0%,#5a6d83 40%,#2f3a48 100%);clip-path:polygon(0 0,540px 0,600px 100%,0 100%)}
.welcome h2{position:absolute;left:655px;top:72px;color:#fff;font-size:36px;font-weight:600;text-transform:uppercase}
.welcome .bar{position:absolute;left:655px;top:140px;width:75px;height:3px;background:#fff}
.welcome p{position:absolute;left:655px;top:178px;width:400px;color:#fff;font-size:14px;line-height:27px}
.welcome .btn{position:absolute;left:655px;top:367px;background:var(--orange);font-size:13px;padding:10px 30px}

/* why choose */
.why{position:absolute;left:144px;top:2295px;width:912px;height:360px}
.why .vline{position:absolute;left:454px;top:0;width:1px;height:360px;background:var(--line)}
.why .hline{position:absolute;left:0;top:180px;width:912px;height:1px;background:var(--line)}
.feat{position:absolute;width:440px;height:170px}
.feat .ico{position:absolute;left:16px;top:30px;width:100px;height:100px;border-radius:50%;background:var(--orange);display:flex;align-items:center;justify-content:center}
.feat h4{position:absolute;left:142px;top:26px;font-size:18px;font-weight:600}
.feat p{position:absolute;left:142px;top:58px;width:290px;font-size:13px;line-height:22px}

/* benefits */
.benefits{position:absolute;left:0;top:2750px;width:1200px;height:720px;background:var(--light)}
.ben{position:absolute;width:240px;font-size:13px;line-height:21px}
.ben h4{font-size:18px;font-weight:600;margin-bottom:6px}
.ben.r{text-align:right}
.ring-node{position:absolute;width:72px;height:72px;border-radius:50%;background:var(--blue);border:5px solid #fff;box-shadow:0 0 0 1px #cfd6e2;display:flex;align-items:center;justify-content:center}
.center-mark{position:absolute;left:498px;top:3070px;width:200px;height:200px;border-radius:50%;background:var(--navy);display:flex;align-items:center;justify-content:center;font-family:"Titillium Web",sans-serif;font-weight:700;font-size:30px;color:#fff;letter-spacing:1px}

/* quote */
.quote{position:absolute;left:0;top:3470px;width:1200px;height:493px;background:linear-gradient(90deg,#1b3f87 0%,#1d5a99 55%,#1a7fae 100%)}
.quote h2{position:absolute;left:144px;top:100px;color:#fff;font-size:38px;line-height:44px;font-weight:700;text-transform:uppercase}
.quote p{position:absolute;left:144px;top:250px;width:300px;color:#fff;font-size:14px;line-height:24px}
.qform{position:absolute;left:487px;top:90px;width:569px;height:298px;border:2px solid #fff}
.qform .f{position:absolute;background:#fff;font-size:11px;color:#333;padding:12px 14px}
.qform .btn{position:absolute;left:26px;top:232px;width:150px;height:40px;line-height:40px;background:var(--orange);font-size:15px}

/* blogs */
.blog-main{position:absolute;left:144px;top:4165px;width:426px;height:475px}
.blog-main .photo{height:290px;background:linear-gradient(180deg,#5f7a44 0%,#c33a76 45%,#b84d8f 100%)}
.blog-main .box{position:absolute;left:10px;top:262px;width:406px;height:213px;border:1px solid var(--line);background:#fff;text-align:center}
.blog-main h4{font-size:17px;line-height:24px;font-weight:600;margin-top:24px;text-transform:uppercase}
.meta{font-size:13px;color:var(--orange);margin-top:10px}
.meta span{margin:0 10px}
.blog-main p{font-size:13px;line-height:22px;padding:0 30px;margin-top:14px}
.blog-side{position:absolute;left:604px;width:452px;height:213px}
.blog-side .photo{position:absolute;left:0;top:0;width:210px;height:213px}
.blog-side .box{position:absolute;left:210px;top:12px;width:242px;height:188px;border:1px solid var(--line);background:#fff;padding:18px 14px 0 14px}
.blog-side h4{font-size:15px;line-height:22px;font-weight:600;text-transform:uppercase}
.blog-side .meta{font-size:12px;margin-top:6px}
.blog-side p{font-size:13px;line-height:21px;margin-top:8px}

/* footer */
.footer{position:absolute;left:0;top:4730px;width:1200px;height:496px;background:var(--footer);color:#ddd}
.footer h4{position:absolute;color:#fff;font-size:17px;font-weight:600;text-transform:uppercase}
.footer .brand{left:120px;top:50px}
.footer .brand span{color:#fff}
.footer p,.footer li{font-size:13px;line-height:22px}
.socials{position:absolute;left:120px;top:270px;display:flex;gap:10px}
.socials i{width:30px;height:30px;border:1.5px solid #fff;border-radius:50%;display:block}
.nl-input{position:absolute;left:402px;top:183px;width:272px;height:38px;background:#fff;border-radius:3px;font-size:11px;color:#777;padding:12px 14px}
.nl-btn{position:absolute;left:402px;top:238px;width:138px;height:36px;line-height:36px;background:var(--orange);font-size:14px}
.contact-row{position:absolute;left:720px;display:flex;gap:14px}
.quick{position:absolute;left:946px;top:80px;list-style:none}
.footer .rule{position:absolute;left:0;top:380px;width:1200px;height:1px;background:#3a3a3a}
.copyright{position:absolute;left:0;top:430px;width:1200px;text-align:center;font-size:13px;color:#ddd}
</style>
</head>
<body>

<header class="header">
  <div class="brand"><div class="dot"></div><span>ALTURO</span></div>
  <div class="tollfree">
    <div class="ico"><svg width="18" height="18" viewBox="0 0 24 24"><path fill="#fff" d="M6.6 10.8a15 15 0 0 0 6.6 6.6l2.2-2.2c.3-.3.7-.4 1-.2 1.1.4 2.3.6 3.6.6.6 0 1 .4 1 1V20c0 .6-.4 1-1 1A17 17 0 0 1 3 4c0-.6.4-1 1-1h3.5c.6 0 1 .4 1 1 0 1.3.2 2.5.6 3.6.1.3 0 .7-.2 1z"/></svg></div>
    <div><small>Toll free :</small><b>+808 555 0142</b></div>
  </div>
  <div class="search">Search here<svg width="16" height="16" viewBox="0 0 24 24"><circle cx="10" cy="10" r="7" fill="none" stroke="#777" stroke-width="2"/><path d="M15 15l6 6" stroke="#777" stroke-width="2"/></svg></div>
  <nav class="navbar"><ul>
    <li class="active">Home</li><li>About Us</li><li>Our Products</li><li>Why Choose Us</li><li>Benefits</li><li>Contact Us</li>
  </ul></nav>
</header>

<section class="hero" role="img" aria-label="Evening view of Quito city below the Andes mountains under a golden sky"></section>
<svg class="abs" style="left:0;top:700px" width="1200" height="120" viewBox="0 0 1200 120">
  <polygon points="620,115 1200,52 1200,73 700,120" fill="var(--orange)"/>
</svg>
<div class="hero-text">
  <h1>Alturo Export</h1>
  <p>Nemo enim ipsam voluptatem quia voluptas sit<br>aspernatur aut odit aut fugit</p>
  <span class="btn">Get a Qoute</span>
</div>
<div class="dots"><i class="on"></i><i></i><i></i></div>

<h2 class="section-title" style="top:866px">Our Products</h2>
<div class="underline" style="top:926px"></div>

<article class="card" style="left:144px">
  <div class="photo" role="img" aria-label="Crates of fresh flowers in a greenhouse" style="background:linear-gradient(180deg,#4e6a3a,#8a6a4a)"></div>
  <div class="badge"><svg width="40" height="40" viewBox="0 0 40 40" fill="none" stroke="#fff" stroke-width="2"><circle cx="20" cy="14" r="7"/><path d="M20 21v14M20 28c-4-4-9-3-9-3M20 30c4-4 9-3 9-3"/></svg></div>
  <h3>Flowers</h3>
  <p>Sed ut perspiciatis unde omnis iste natus error sit voluptatem accusantium doloremque laudantium, totam rem aperiam, eaque ipsa quae ab illo inventore veritatis et quasi</p>
  <span class="btn">Read More</span>
</article>
<article class="card" style="left:459px">
  <div class="photo" role="img" aria-label="Assorted chocolates in an open gift box" style="background:linear-gradient(180deg,#b9aea4,#5a3a28)"></div>
  <div class="badge"><svg width="40" height="40" viewBox="0 0 40 40" fill="none" stroke="#fff" stroke-width="2"><rect x="10" y="8" width="20" height="26" rx="2"/><path d="M10 17h20M10 25h20M20 8v26"/></svg></div>
  <h3>Chocolate</h3>
  <p>Sed ut perspiciatis unde omnis iste natus error sit voluptatem accusantium doloremque laudantium, totam rem aperiam, eaque ipsa quae ab illo inventore veritatis et quasi</p>
  <span class="btn">Read More</span>
</article>
<article class="card" style="left:774px">
  <div class="photo" role="img" aria-label="Bunch of ripe bananas on a blue wooden table" style="background:linear-gradient(135deg,#2d5f8a,#e8c53a 60%,#2d5f8a)"></div>
  <div class="badge"><svg width="40" height="40" viewBox="0 0 40 40" fill="none" stroke="#fff" stroke-width="2"><path d="M10 12c0 12 8 20 20 18M14 10c2 10 8 15 17 14M28 6l2 4"/></svg></div>
  <h3>Bananas</h3>
  <p>Sed ut perspiciatis unde omnis iste natus error sit voluptatem accusantium doloremque laudantium, totam rem aperiam, eaque ipsa quae ab illo inventore veritatis et quasi</p>
  <span class="btn">Read More</span>
</article>

<section class="welcome">
  <div class="photo" role="img" aria-label="Businessman holding a tablet over a shipping container yard with a global network overlay"></div>
  <h2>Welcome to Alturo</h2>
  <div class="bar"></div>
  <p>Nemo enim ipsam voluptatem quia voluptas sit aspernatur aut odit aut fugit, sed quia consequuntur magni dolores eos qui ratione voluptatem sequi nesciunt. Neque porro quisquam est, qui dolorem ipsum quia dolor sit amet, cor, adipisci velit, sed quia non numquam eius modi tempora incidunt ut labore et dolore magnam aliquam</p>
  <span class="btn">Read More</span>
</section>

<h2 class="section-title" style="top:2156px">Why Choose Alturo?</h2>
<div class="underline" style="top:2224px"></div>

<div class="why">
  <div class="vline"></div><div class="hline"></div>
  <div class="feat" style="left:0;top:0">
    <div class="ico"><svg width="50" height="50" viewBox="0 0 50 50" fill="none" stroke="#fff" stroke-width="2"><rect x="8" y="10" width="34" height="26" rx="2"/><circle cx="25" cy="23" r="8"/><path d="M25 18v10M18 42h14"/></svg></div>
    <h4>Best Prices</h4>
    <p>Lorem ipsum dolor sit amet, consectetur adipiscing elit, sed do eiusmod tempor incididunt ut labore et dolore magna aliqua. Ut enim ad minim veniam</p>
  </div>
  <div class="feat" style="left:468px;top:0">
    <div class="ico"><svg width="50" height="50" viewBox="0 0 50 50" fill="none" stroke="#fff" stroke-width="2"><path d="M25 6l15 6v12c0 10-7 16-15 20-8-4-15-10-15-20V12z"/><path d="M18 25l5 5 10-10"/></svg></div>
    <h4>Your Satisfaction Guaranteed</h4>
    <p>Lorem ipsum dolor sit amet, consectetur adipiscing elit, sed do eiusmod tempor incididunt ut labore et dolore magna aliqua. Ut enim ad minim veniam</p>
  </div>
  <div class="feat" style="left:0;top:192px">
    <div class="ico"><svg width="50" height="50" viewBox="0 0 50 50" fill="none" stroke="#fff" stroke-width="2"><circle cx="25" cy="20" r="12"/><path d="M25 13l2 5h5l-4 3 2 5-5-3-5 3 2-5-4-3h5zM17 30l-4 12 6-3 3 5 3-10M33 30l4 12-6-3-3 5-3-10"/></svg></div>
    <h4>Highest Quality</h4>
    <p>Lorem ipsum dolor sit amet, consectetur adipiscing elit, sed do eiusmod tempor incididunt ut labore et dolore magna aliqua. Ut enim ad minim veniam</p>
  </div>
  <div class="feat" style="left:468px;top:192px">
    <div class="ico"><svg width="50" height="50" viewBox="0 0 50 50" fill="none" stroke="#fff" stroke-width="2"><path d="M6 42V24l10-6v6l10-6v6l10-6V8h6v34z"/><path d="M12 34h4M20 34h4M28 34h4"/></svg></div>
    <h4>Industry Leaders</h4>
    <p>Lorem ipsum dolor sit amet, consectetur adipiscing elit, sed do eiusmod tempor incididunt ut labore et dolore magna aliqua. Ut enim ad minim veniam</p>
  </div>
</div>

<section class="benefits"></section>
<h2 class="section-title" style="top:2816px">Alturo Benefits</h2>
<div class="underline" style="top:2884px"></div>
<svg class="abs" style="left:378px;top:2950px" width="440" height="440" viewBox="0 0 440 440">
  <circle cx="220" cy="220" r="205" fill="none" stroke="var(--blue)" stroke-width="5"/>
</svg>
<div class="center-mark">ALTURO</div>
<div class="ring-node" style="left:397px;top:2978px"><svg width="32" height="32" viewBox="0 0 32 32" fill="none" stroke="#fff" stroke-width="2"><rect x="12" y="4" width="8" height="7"/><rect x="3" y="22" width="8" height="7"/><rect x="21" y="22" width="8" height="7"/><path d="M16 11v5M7 22v-6h18v6"/></svg></div>
<div class="ring-node" style="left:357px;top:3120px"><svg width="30" height="30" viewBox="0 0 24 24"><path fill="#fff" d="M12 2a7 7 0 0 0-7 7c0 5 7 13 7 13s7-8 7-13a7 7 0 0 0-7-7zm0 9.5A2.5 2.5 0 1 1 12 6.5a2.5 2.5 0 0 1 0 5z"/></svg></div>
<div class="ring-node" style="left:413px;top:3254px"><svg width="30" height="30" viewBox="0 0 32 32" fill="none" stroke="#fff" stroke-width="2"><rect x="7" y="3" width="18" height="26" rx="2"/><path d="M11 10h10M11 16h10M11 22h6"/></svg></div>
<div class="ring-node" style="left:725px;top:2978px"><svg width="32" height="32" viewBox="0 0 32 32" fill="none" stroke="#fff" stroke-width="2"><path d="M4 28h24M8 24v-8M13 24V10M18 24v-6M23 24V7"/></svg></div>
<div class="ring-node" style="left:765px;top:3120px"><svg width="32" height="32" viewBox="0 0 32 32" fill="none" stroke="#fff" stroke-width="2"><circle cx="16" cy="16" r="12"/><path d="M4 16h24M16 4c-5 6-5 18 0 24M16 4c5 6 5 18 0 24"/></svg></div>
<div class="ring-node" style="left:709px;top:3254px"><svg width="32" height="32" viewBox="0 0 32 32" fill="none" stroke="#fff" stroke-width="2"><rect x="4" y="5" width="24" height="18"/><path d="M8 19l5-6 4 3 6-7M12 28h8"/></svg></div>
<div class="ben r" style="left:136px;top:2980px"><h4>Operations:</h4>Sed ut perspiciatis unde omnis iste natus voluptatem accusantium doloremque laudantium</div>
<div class="ben r" style="left:136px;top:3116px"><h4>Matching:</h4>Sed ut perspiciatis unde omnis iste natus voluptatem accusantium doloremque laudantium</div>
<div class="ben r" style="left:150px;top:3260px"><h4>Billing:</h4>Sed ut perspiciatis unde omnis iste natus voluptatem accusantium doloremque laudantium</div>
<div class="ben" style="left:820px;top:2980px"><h4>Analytics</h4>Sed ut perspiciatis unde omnis iste natus voluptatem accusantium doloremque laudantium</div>
<div class="ben" style="left:864px;top:3116px"><h4>Logistics Report</h4>Sed ut perspiciatis unde omnis iste natus voluptatem accusantium doloremque laudantium</div>
<div class="ben" style="left:807px;top:3252px"><h4>Marketplace</h4>Sed ut perspiciatis unde omnis iste natus voluptatem accusantium doloremque laudantium</div>

<section class="quote">
  <h2>Get Your Free<br>Quote</h2>
  <p>Sed ut perspiciatis unde omnis iste natus sit voluptatem accusantium doloremque laudantium, totam rem aperiam, eaque ipsa quae ab illo inventore veritatis et quasi architecto beatae vitae dicta</p>
  <div class="qform">
    <div class="f" style="left:26px;top:24px;width:252px;height:40px">First name</div>
    <div class="f" style="left:290px;top:24px;width:252px;height:40px">Last Name</div>
    <div class="f" style="left:26px;top:74px;width:252px;height:40px">Email</div>
    <div class="f" style="left:290px;top:74px;width:252px;height:40px">Phone Number</div>
    <div class="f" style="left:26px;top:124px;width:516px;height:92px">Message</div>
    <span class="btn">Submit</span>
  </div>
</section>

<h2 class="section-title" style="top:4032px">Latest Blogs</h2>
<div class="underline" style="top:4100px"></div>

<article class="blog-main">
  <div class="photo" role="img" aria-label="Rows of pink and purple flowers in a nursery"></div>
  <div class="box">
    <h4>Sed ut perspiciatis unde omnis<br>sit voluptatem accusan</h4>
    <div class="meta"><span>Jan 25, 2020</span>|<span>2 Comments</span>|<span>by Marta</span></div>
    <p>Sed ut perspiciatis unde omnis iste natus error sit voluptatem accusantium doloremque laudantium, totam rem aperiam, eaque ipsa quae</p>
  </div>
</article>
<article class="blog-side" style="top:4165px">
  <div class="photo" role="img" aria-label="Stacked cardboard shipping boxes" style="background:linear-gradient(135deg,#d9c7a8,#9b7443)"></div>
  <div class="box">
    <h4>Nemo enim ipsam volup<br>quia voluptas</h4>
    <div class="meta">Jan 25, 2020 &nbsp;|&nbsp; 2 comments</div>
    <p>Sed ut perspiciatis unde omnis iste natus error sit vuptatem accusantium doloremque</p>
  </div>
</article>
<article class="blog-side" style="top:4405px">
  <div class="photo" role="img" aria-label="Warehouse worker checking documents between storage racks" style="background:linear-gradient(135deg,#c9ccd0,#6b7480)"></div>
  <div class="box">
    <h4>Nemo enim ipsam volup<br>quia voluptas</h4>
    <div class="meta">Jan 25, 2020 &nbsp;|&nbsp; 2 comments</div>
    <p>Sed ut perspiciatis unde omnis iste natus error sit vuptatem accusantium doloremque</p>
  </div>
</article>

<footer class="footer">
  <div class="brand"><div class="dot" style="background:#2b5ca8"></div><span>ALTURO</span></div>
  <p class="abs" style="left:120px;top:150px;width:240px">Sed ut perspiciatis unde omnis iste natus error sit voluptatem accusantium doloremque laudantium, totam rem aperiam, eaque ipsa quae</p>
  <div class="socials"><i></i><i></i><i></i><i></i></div>

  <h4 style="left:402px;top:70px">Sign up for Newsletter</h4>
  <p class="abs" style="left:402px;top:108px;width:280px">excepteur sint occaecat cupidatat non proident, sunt in culpa qui officia deserunt</p>
  <div class="nl-input">Enter email</div>
  <span class="btn nl-btn">Subscribe</span>

  <h4 style="left:720px;top:70px">Contact Us</h4>
  <div class="contact-row" style="top:118px"><svg width="18" height="20" viewBox="0 0 24 24"><path fill="#fff" d="M12 2a7 7 0 0 0-7 7c0 5 7 13 7 13s7-8 7-13a7 7 0 0 0-7-7zm0 9.5A2.5 2.5 0 1 1 12 6.5a2.5 2.5 0 0 1 0 5z"/></svg><p>Alturo<br>PO Box 410<br>Linden Falls, RI 02900</p></div>
  <div class="contact-row" style="top:210px"><svg width="18" height="18" viewBox="0 0 24 24"><path fill="#fff" d="M6.6 10.8a15 15 0 0 0 6.6 6.6l2.2-2.2c.3-.3.7-.4 1-.2 1.1.4 2.3.6 3.6.6.6 0 1 .4 1 1V20c0 .6-.4 1-1 1A17 17 0 0 1 3 4c0-.6.4-1 1-1h3.5c.6 0 1 .4 1 1 0 1.3.2 2.5.6 3.6.1.3 0 .7-.2 1z"/></svg><p>Phone:<br>(808) 555-0177</p></div>
  <div class="contact-row" style="top:262px"><svg width="18" height="18" viewBox="0 0 24 24"><path fill="#fff" d="M2 5h20v14H2zm2 2v.5l8 5 8-5V7z"/></svg><p>Email:<br>info@alturo-export.net</p></div>

  <h4 style="left:942px;top:70px">Quick Links</h4>
  <ul class="quick"><li>Home</li><li>About Us</li><li>Our Products</li><li>Why choose us?</li><li>Blog</li><li>Contact Us</li></ul>

  <div class="rule"></div>
  <div class="copyright">Alturo © 2020 All Rights Reserved | Privacy Policy | Terms and Conditions</div>
</footer>

</body>
</html>
```